Hollow Thicket, a 3d voxel survival video game needs a card for gaming conventions

I am the lead developer for Hollow Thicket http://www.HollowThicket.example and need a business card to hand out at an indie gaming convention
The card would need to include the game name, website url, my name, position (Lead Developer), e-mail and phone number
The game is a 3d, voxel (with smooth terrain) based survival game with guns and wildlife. The main icon of the game would likely be a grizzly bear but I am willing to accept other designs too.
Attached is a media kit for the game with some images you can use but don't have to its just what little art I can provide. Anything on the website or from the video game can also be used. unrelated art can also be used.
Target Market(s)
Indie Developers/publishers at conferences
Industry/Entity Type
Games
Contact Information for Business Card
Name: Corin Waldrick
Position: Lead Developer
E-mail: Pale_Kettle@mailbox.example
Phone number: 555-372-1186

```html
<!DOCTYPE html>
<html lang="en">
<head>
<meta charset="utf-8">
<title>Hollow Thicket – Business Card</title>
<link rel="stylesheet" href="https://fonts.googleapis.com/css2?family=Open+Sans:wght@400;700&display=swap">
<style>
  :root {
    --page-bg: #d9d6d0;
    --card-light: #e9e1c6;
    --card-mid: #8a8458;
    --card-dark: #2f2c0e;
    --band-red: #c4301c;
    --band-orange: #e0703a;
    --band-tan: #c79a6a;
    --ink: #1a1a14;
    --logo-red: #a52716;
    --bear-light: #8a5530;
    --bear-dark: #3a2414;
  }
  * { box-sizing: border-box; margin: 0; padding: 0; }
  html, body {
    width: 1200px;
    height: 844px;
    overflow: hidden;
    background: var(--page-bg);
    font-family: "Open Sans", Arial, sans-serif;
  }
  .sheet {
    width: 1200px;
    height: 844px;
    display: flex;
    align-items: center;
    justify-content: center;
    gap: 40px;
  }
  .card {
    position: relative;
    width: 540px;
    height: 310px;
    overflow: hidden;
    background: radial-gradient(ellipse 60% 65% at 55% 45%, var(--card-light) 0%, var(--card-mid) 55%, var(--card-dark) 100%);
    box-shadow: 0 6px 18px rgba(0,0,0,0.25);
  }

  /* Front */
  .edge-band {
    position: absolute;
    left: 0;
    width: 100%;
    height: 12px;
    background: linear-gradient(to bottom, var(--band-red), var(--band-orange));
  }
  .edge-band--top { top: 0; }
  .edge-band--bottom { bottom: 0; background: linear-gradient(to top, var(--band-red), var(--band-orange)); }
  .mascot-photo {
    position: absolute;
    left: 20px;
    bottom: 12px;
    width: 250px;
    height: 240px;
    border-radius: 46% 40% 0 0;
    background: radial-gradient(ellipse 60% 70% at 50% 40%, var(--bear-light) 0%, var(--bear-dark) 80%, rgba(58,36,20,0) 100%);
  }
  .contact {
    position: absolute;
    left: 280px;
    top: 92px;
    width: 230px;
    text-align: center;
    color: var(--ink);
  }
  .contact__name { font-weight: 700; font-size: 16px; line-height: 1.2; }
  .contact__role { font-size: 12px; line-height: 1.3; }
  .contact__details { margin-top: 22px; font-size: 13px; line-height: 1.5; }

  /* Back */
  .edge-tab {
    position: absolute;
    width: 36px;
    height: 34px;
    background: linear-gradient(to bottom, var(--band-red), var(--band-tan));
  }
  .edge-tab--left { left: 0; bottom: 78px; }
  .edge-tab--right { right: 0; top: 52px; }
  .brand {
    position: absolute;
    inset: 0;
    display: flex;
    flex-direction: column;
    align-items: center;
    justify-content: center;
  }
  .game-title {
    display: flex;
    flex-direction: column;
    align-items: center;
    color: var(--logo-red);
    font-weight: 700;
    font-size: 52px;
    line-height: 1.05;
    letter-spacing: 3px;
    text-transform: uppercase;
  }
  .game-url {
    margin-top: 14px;
    font-size: 13px;
    color: var(--ink);
    letter-spacing: 0.5px;
  }
</style>
</head>
<body>
  <main class="sheet">
    <section class="card card--front">
      <div class="edge-band edge-band--top"></div>
      <div class="mascot-photo" role="img" aria-label="Photo of a roaring grizzly bear"></div>
      <div class="contact">
        <p class="contact__name">Corin Waldrick</p>
        <p class="contact__role">Lead Developer</p>
        <p class="contact__details">555-372-1186<br>Pale_Kettle@mailbox.example</p>
      </div>
      <div class="edge-band edge-band--bottom"></div>
    </section>

    <section class="card card--back">
      <div class="edge-tab edge-tab--right"></div>
      <div class="brand">
        <h1 class="game-title"><span>Hollow</span><span>Thicket</span></h1>
        <p class="game-url">www.HollowThicket.example</p>
      </div>
      <div class="edge-tab edge-tab--left"></div>
    </section>
  </main>
</body>
</html>
```